We need a new business card that reflects who we are. Professional, classy, modern, and service ori

We need a business card design for a window coverings design company in Kansas City called Bright Lane Interiors. We offer professional, modern, and high quality window covering products. We are looking to portray an image of a big, national franchise. We are a 5 location (with showrooms) business with 10 professional designers and 4 professional installers. These cards will be used with Thank you cards, given to realtors, and asked for referrals with.

Target Market(s)

Kansas City

Industry/Entity Type

Business

Contact Information for Business Card

We would like our card to look clean and simple on the front, featuring our logo and Marlow Fenwick's. Our designers' phone numbers and emails should be displayed as well as their title.

Font styles to use
Sans Serif

Colors

Designer to choose colors to be used in the design.

Requirements
Must have
• Front - Logos, name, phone number, email address
• Back - Showroom locations, social media? Appt date/time?
Nice to have
• I would like a clean and modern look (not contemporary. I like a white background, but I am open to ideas. Looking for a "National chain" look for a small business.
Should not have
• Too much busyness.

```html
<!DOCTYPE html>
<html lang="en">
<head>
<meta charset="utf-8">
<title>Bright Lane Interiors – Business Card</title>
<link rel="stylesheet" href="https://fonts.googleapis.com/css2?family=Roboto:wght@400;500;700&family=Roboto+Condensed:wght@400;500;700&display=swap">
<style>
  :root {
    --backdrop: #2a2a2a;
    --card: #f3f3f3;
    --red: #c8373b;
    --grey-band: #8e9094;
    --ink: #141414;
    --text-grey: #4a4a4a;
    --soft-grey: #6b6d70;
    --rule: #c9c9c9;
  }
  * { box-sizing: border-box; margin: 0; padding: 0; }
  html, body { width: 1200px; height: 960px; overflow: hidden; }
  body {
    background: var(--backdrop);
    position: relative;
    font-family: "Roboto", Arial, sans-serif;
  }
  .card {
    position: absolute;
    width: 600px;
    height: 342px;
    background: var(--card);
  }
  .card--front { left: 322px; top: 108px; }
  .card--back { left: 320px; top: 493px; }

  /* Front */
  .brand {
    position: absolute;
    left: 40px;
    top: 132px;
    width: 270px;
    text-align: center;
  }
  .brand__name {
    display: flex;
    align-items: center;
    justify-content: center;
    gap: 8px;
    font-family: "Roboto Condensed", Arial, sans-serif;
    font-weight: 700;
    font-size: 27px;
    color: var(--ink);
    line-height: 1;
  }
  .brand__mark {
    width: 18px;
    height: 18px;
    background: var(--red);
  }
  .brand__tagline {
    margin-top: 12px;
    font-size: 12px;
    color: var(--ink);
  }
  .divider {
    position: absolute;
    left: 316px;
    top: 110px;
    width: 1px;
    height: 127px;
    background: var(--rule);
  }
  .contact {
    position: absolute;
    left: 344px;
    top: 114px;
  }
  .contact__name {
    font-family: "Roboto Condensed", Arial, sans-serif;
    font-weight: 500;
    font-size: 25px;
    color: var(--red);
    line-height: 1.1;
  }
  .contact__title {
    font-weight: 500;
    font-size: 15px;
    color: var(--ink);
    letter-spacing: 0.4px;
    margin-top: 1px;
  }
  .contact__lines {
    margin-top: 9px;
    list-style: none;
    font-size: 14.5px;
    color: var(--text-grey);
    line-height: 19.5px;
  }
  .band {
    position: absolute;
    left: 0;
    bottom: 0;
    width: 100%;
    height: 13px;
    display: flex;
    gap: 2px;
  }
  .band__part { flex: 1; background: var(--grey-band); }
  .band__part--accent { background: var(--red); }

  /* Back */
  .partner {
    position: absolute;
    top: 41px;
    left: 0;
    width: 100%;
    text-align: center;
    font-family: "Roboto Condensed", Arial, sans-serif;
    font-weight: 500;
    font-size: 16px;
    color: var(--soft-grey);
  }
  .appointments {
    position: absolute;
    left: 82px;
    top: 78px;
    width: 440px;
    list-style: none;
  }
  .appointment {
    height: 45.5px;
    line-height: 28px;
    color: var(--red);
    white-space: nowrap;
  }
  .appointment__label { font-size: 17px; }
  .appointment__blank {
    display: inline-block;
    vertical-align: baseline;
    height: 1px;
    border-bottom: 1px dotted var(--soft-grey);
    margin: 0 3px 0 5px;
  }
  .appointment__blank--date { width: 166px; }
  .appointment__blank--time { width: 106px; }
  .appointment__suffix { font-size: 13px; }
  .showrooms {
    position: absolute;
    left: 0;
    top: 259px;
    width: 100%;
    text-align: center;
    font-family: "Roboto Condensed", Arial, sans-serif;
  }
  .showrooms__title {
    font-weight: 700;
    font-size: 16px;
    color: var(--red);
  }
  .showrooms__list {
    margin-top: 3px;
    font-size: 14px;
    color: var(--text-grey);
  }
  .social {
    margin-top: 5px;
    display: flex;
    justify-content: center;
    gap: 3px;
    list-style: none;
  }
  .social__dot {
    width: 20px;
    height: 20px;
    border-radius: 50%;
    background: var(--red);
  }
</style>
</head>
<body>

  <section class="card card--front" aria-label="Business card front">
    <div class="brand">
      <div class="brand__name"><span class="brand__mark"></span>Bright Lane Interiors</div>
      <p class="brand__tagline">Blinds, Shades, Shutters, Draperies &amp; Decor</p>
    </div>
    <div class="divider"></div>
    <div class="contact">
      <h1 class="contact__name">JANE CARTER</h1>
      <p class="contact__title">DESIGNER</p>
      <ul class="contact__lines">
        <li>P. 913.555.0148</li>
        <li>info@brightlaneinteriors.com</li>
        <li>www.brightlaneinteriors.com</li>
      </ul>
    </div>
    <div class="band">
      <span class="band__part"></span>
      <span class="band__part band__part--accent"></span>
      <span class="band__part"></span>
    </div>
  </section>

  <section class="card card--back" aria-label="Business card back">
    <p class="partner">Marlow Fenwick Gallery</p>
    <ul class="appointments">
      <li class="appointment"><span class="appointment__label">Date :</span><span class="appointment__blank appointment__blank--date"></span><span class="appointment__label">Time :</span><span class="appointment__blank appointment__blank--time"></span><span class="appointment__suffix">AM/PM</span></li>
      <li class="appointment"><span class="appointment__label">Date :</span><span class="appointment__blank appointment__blank--date"></span><span class="appointment__label">Time :</span><span class="appointment__blank appointment__blank--time"></span><span class="appointment__suffix">AM/PM</span></li>
      <li class="appointment"><span class="appointment__label">Date :</span><span class="appointment__blank appointment__blank--date"></span><span class="appointment__label">Time :</span><span class="appointment__blank appointment__blank--time"></span><span class="appointment__suffix">AM/PM</span></li>
      <li class="appointment"><span class="appointment__label">Date :</span><span class="appointment__blank appointment__blank--date"></span><span class="appointment__label">Time :</span><span class="appointment__blank appointment__blank--time"></span><span class="appointment__suffix">AM/PM</span></li>
    </ul>
    <div class="showrooms">
      <h2 class="showrooms__title">SHOWROOM LOCATIONS</h2>
      <p class="showrooms__list">WESTBROOK | ASHFORD PARK | CEDAR HILL | NORTHGATE | MILLBROOK</p>
      <ul class="social" aria-label="Social media">
        <li class="social__dot"></li>
        <li class="social__dot"></li>
        <li class="social__dot"></li>
        <li class="social__dot"></li>
      </ul>
    </div>
  </section>

</body>
</html>
```